BrivoNest Learning App for Children with Dyslexia

Project Description:

We are seeking a talented UI/UX designer to create engaging and intuitive designs for Brivonest, an innovative educational app designed to help children learn letters and words through a multisensory learning approach. The app aims to be particularly helpful for children with dyslexia, providing a supportive and interactive learning environment.

Key App Features & Design Requirements:

Account Creation Screen: Design a welcoming and straightforward sign-up page that allows users to register with their email or continue with Quarnix. The design should be clean, focusing on user-friendliness and accessibility, adhering to our terms of service and privacy policy.

Main Screen Design: The main screen should allocate at least 4/6 of its height to the interactive drawing area. It needs to display word prompts in both correct and scrambled orders and include options to "Show all Words," "Play all words," and a search function. The interface should be vibrant, engaging, and easy to navigate for children.

Profile Section: Create a user-friendly profile page that allows users to edit their profile image, name, username, email, links, and bio. The design should be clean and encourage user engagement.

BrivoTally Page: This section will display the user's learning progress, including rankings, a learning curve, and recently learned words. It should visually represent progress in a motivating and understandable way, suitable for a younger audience.

Visual and Auditory Feedback Implementation: Incorporate elements that support visual and auditory feedback, using dyslexia-friendly formats. This includes choosing appropriate colors, fonts, and auditory cues.

Accessibility and Customization Settings: Designs should include settings for adjusting visual contrast, font size, and the word list to accommodate individual preferences and needs.

Feel free to add more interactions and/or pages.

Design preferences:

Color Scheme: Use a bright, inviting color palette that stimulates learning and engagement without overwhelming the users.
Font Selection: Opt for fonts that are readable and accessible, particularly for users with dyslexia.
Icons and Graphics: Design custom icons and graphics that are cohesive with the app's theme and purpose. Illustrations should be simple, relatable, and supportive of the learning process.

Target Market(s)

Educational

Industry/Entity Type

Educational

Colors
0054AA
0677BA
7BADD7
CADEEF
E8F1F8
0094D4
00A9DD
6FCCEA
C7EBF8
E9F6FB

Requirements
Must have
• Educational app, a writing area, scoring and account management
Nice to have
• Statistics, Ranking Page, Settings and some nice visual features

```html
<!DOCTYPE html>
<html lang="en">
<head>
<meta charset="utf-8">
<title>Brivonest – App Screens</title>
<link href="https://fonts.googleapis.com/css2?family=Roboto:wght@400;500;700&family=Ubuntu:wght@500&display=swap" rel="stylesheet">
<style>
  :root{
    --brand-deep:#0054AA;
    --brand-mid:#0677BA;
    --brand-soft:#7BADD7;
    --brand-pale:#CADEEF;
    --brand-mist:#E8F1F8;
    --sky:#00A9DD;
    --sky-light:#6FCCEA;
    --sky-pale:#C7EBF8;
    --ink:#1c1c1c;
    --muted:#555;
    --line:#dcdcdc;
    --canvas:#E8F1F8;
    --screen:#ffffff;
  }
  *{box-sizing:border-box;margin:0;padding:0}
  html,body{width:1200px;height:773px;overflow:hidden}
  body{background:var(--canvas);font-family:"Roboto",sans-serif;color:var(--ink);position:relative}
  .screen{position:absolute;top:36px;width:324px;height:700px;background:var(--screen);border-radius:36px;box-shadow:0 10px 30px rgba(0,40,80,.15);overflow:hidden}
  .screen--signup{left:57px}
  .screen--main{left:438px}
  .screen--profile{left:819px}
  .abs{position:absolute}
  .status-bar{position:absolute;top:8px;left:18px;right:18px;height:16px;display:flex;justify-content:space-between;align-items:center;font-size:12px;font-weight:500}
  .app-title{position:absolute;left:0;right:0;text-align:center;font-family:"Ubuntu",sans-serif;font-weight:500;font-size:19px;color:var(--brand-mid)}
  .center{left:0;right:0;text-align:center}

  /* sign up */
  .hero-art{left:17px;top:66px;width:291px;height:288px;border-radius:19px;background:radial-gradient(circle at 50% 32%,#c7ebf8 0,#6fccea 38%,#1da6d6 100%)}
  .kids-band{left:14px;top:378px;width:296px;height:92px;background:linear-gradient(90deg,#f3e6d8,#fff 30%,#fff 70%,#f3e6d8)}
  .create-title{top:425px;font-size:12.5px;font-weight:500;color:var(--brand-mid);letter-spacing:.2px}
  .hint{top:491px;font-size:10px;color:#333}
  .email-input{left:41px;top:518px;width:242px;height:26px;border:1px solid #e6e6e6;border-radius:6px;background:#fafafa;font-size:8px;color:#666;padding:8px 12px}
  .btn-primary{background:var(--brand-deep);color:#fff;border-radius:20px;display:flex;align-items:center;justify-content:center;font-size:12px;font-weight:500}
  .btn-signup{left:42px;top:555px;width:243px;height:30px}
  .or-line{top:596px;font-size:10px;color:#444}
  .provider{left:130px;top:618px;width:64px;height:30px;display:flex;align-items:center;justify-content:center;gap:4px;font-size:10px;font-weight:500;color:var(--brand-deep)}
  .provider-dot{width:8px;height:8px;border-radius:50%;background:var(--brand-deep)}
  .legal{font-size:7.5px;color:#444}
  .legal a{color:var(--brand-deep)}

  /* main */
  .menu-icon{left:18px;top:87px}
  .tab-title{top:86px;font-size:12.5px;font-weight:500}
  .tab-underline{top:105px;left:147px;width:30px;height:2px;background:var(--brand-deep)}
  .points{right:17px;top:86px;font-size:12.5px}
  .draw-area{left:18px;top:128px;width:287px;height:248px;border:1.5px dashed #d9d9d9;border-radius:2px}
  .btn-outline,.btn-fill{top:410px;height:27px;width:110px;font-size:9.5px;font-weight:500;display:flex;align-items:center;justify-content:center;border-radius:2px;letter-spacing:.2px}
  .btn-outline{left:47px;border:1px solid var(--brand-deep);color:var(--brand-deep)}
  .btn-fill{left:167px;background:var(--brand-deep);color:#fff}
  .word-tile{width:89px;height:40px;border-radius:6px;background:#fff;box-shadow:0 2px 8px rgba(0,0,0,.09);display:flex;align-items:center;justify-content:center;font-size:9.5px;font-weight:500}
  .word-tile--active{background:var(--brand-deep);color:#fff}
  .btn-results{left:42px;top:615px;width:243px;height:29px}

  /* profile */
  .back-btn{left:18px;top:81px;width:24px;height:24px;border-radius:50%;background:#eee;display:flex;align-items:center;justify-content:center}
  .avatar{left:123px;top:129px;width:78px;height:78px;border-radius:50%;background:radial-gradient(circle at 50% 40%,#c89a72,#3f5a3c 70%,#2b3d2a)}
  .edit-link{top:219px;font-size:9.5px;color:#333;text-decoration:underline}
  .field-label{left:18px;font-size:9.5px;font-weight:700;display:flex;align-items:center;gap:4px}
  .field-value{left:134px;width:162px;font-size:7.8px;color:#555;border-bottom:1px solid var(--line);padding-bottom:5px;display:flex;justify-content:space-between}
</style>
</head>
<body>

<!-- Sign up screen -->
<section class="screen screen--signup">
  <div class="status-bar"><span>12:00</span>
    <svg width="54" height="10" viewBox="0 0 54 10"><g fill="#111"><rect x="0" y="6" width="2" height="4"/><rect x="3" y="4" width="2" height="6"/><rect x="6" y="2" width="2" height="8"/><rect x="9" y="0" width="2" height="10"/></g><path d="M15 4a8 8 0 0 1 11 0M17 6a5 5 0 0 1 7 0M19.5 8.5a1.5 1.5 0 0 1 2 0" stroke="#111" stroke-width="1.4" fill="none"/><rect x="31" y="1" width="19" height="8" rx="2" fill="none" stroke="#111"/><rect x="33" y="3" width="15" height="4" fill="#111"/><rect x="51" y="3.5" width="1.5" height="3" fill="#111"/></svg>
  </div>
  <h1 class="app-title" style="top:30px">Brivonest</h1>
  <div class="abs hero-art" role="img" aria-label="Illustration of two graduates standing on an open book held by a hand, under a glowing lightbulb"></div>
  <div class="abs kids-band" role="img" aria-label="Illustration of a row of cheerful children holding a banner"></div>
  <p class="abs center create-title">CREATE AN ACCOUNT</p>
  <p class="abs center hint">Enter your email to sign up for this app</p>
  <div class="abs email-input">email@mailbox.test</div>
  <div class="abs btn-primary btn-signup">Sign Up With Email</div>
  <p class="abs center or-line">or Continue With</p>
  <div class="abs provider"><span class="provider-dot"></span>Quarnix</div>
  <p class="abs center legal" style="top:660px">By clicking continue, you agree to our and <a href="#">Terms of Service</a></p>
  <p class="abs center legal" style="top:677px"><a href="#">Privacy Policy</a></p>
</section>

<!-- Main screen -->
<section class="screen screen--main">
  <div class="status-bar"><span>12:00</span>
    <svg width="54" height="10" viewBox="0 0 54 10"><g fill="#111"><rect x="0" y="6" width="2" height="4"/><rect x="3" y="4" width="2" height="6"/><rect x="6" y="2" width="2" height="8"/><rect x="9" y="0" width="2" height="10"/></g><path d="M15 4a8 8 0 0 1 11 0M17 6a5 5 0 0 1 7 0M19.5 8.5a1.5 1.5 0 0 1 2 0" stroke="#111" stroke-width="1.4" fill="none"/><rect x="31" y="1" width="19" height="8" rx="2" fill="none" stroke="#111"/><rect x="33" y="3" width="15" height="4" fill="#111"/><rect x="51" y="3.5" width="1.5" height="3" fill="#111"/></svg>
  </div>
  <h1 class="app-title" style="top:48px">Brivonest</h1>
  <svg class="abs menu-icon" width="16" height="14" viewBox="0 0 16 14"><g fill="#222"><rect y="0" width="16" height="2.4"/><rect y="5.8" width="16" height="2.4"/><rect y="11.6" width="16" height="2.4"/></g></svg>
  <p class="abs center tab-title">Main Screen</p>
  <div class="abs tab-underline"></div>
  <p class="abs points">16 Points</p>
  <div class="abs draw-area" aria-label="Drawing area"></div>
  <div class="abs btn-outline">SHOW ALL WORDS</div>
  <div class="abs btn-fill">PLAY ALL WORDS</div>
  <div class="abs word-tile" style="left:18px;top:465px">Word 01</div>
  <div class="abs word-tile" style="left:118px;top:465px">Word 02</div>
  <div class="abs word-tile" style="left:217px;top:465px">Word 03</div>
  <div class="abs word-tile word-tile--active" style="left:18px;top:518px">Word 04</div>
  <div class="abs word-tile" style="left:118px;top:518px">.....</div>
  <div class="abs btn-primary btn-results">Show Me The Results</div>
</section>

<!-- Profile screen -->
<section class="screen screen--profile">
  <div class="status-bar"><span>12:00</span>
    <svg width="54" height="10" viewBox="0 0 54 10"><g fill="#111"><rect x="0" y="6" width="2" height="4"/><rect x="3" y="4" width="2" height="6"/><rect x="6" y="2" width="2" height="8"/><rect x="9" y="0" width="2" height="10"/></g><path d="M15 4a8 8 0 0 1 11 0M17 6a5 5 0 0 1 7 0M19.5 8.5a1.5 1.5 0 0 1 2 0" stroke="#111" stroke-width="1.4" fill="none"/><rect x="31" y="1" width="19" height="8" rx="2" fill="none" stroke="#111"/><rect x="33" y="3" width="15" height="4" fill="#111"/><rect x="51" y="3.5" width="1.5" height="3" fill="#111"/></svg>
  </div>
  <h1 class="app-title" style="top:48px">Brivonest</h1>
  <div class="abs back-btn"><svg width="8" height="10" viewBox="0 0 8 10"><path d="M6 1L2 5l4 4" stroke="#222" stroke-width="1.6" fill="none"/></svg></div>
  <p class="abs center tab-title">Profile</p>
  <div class="abs tab-underline"></div>
  <div class="abs avatar" role="img" aria-label="Profile photo of the user"></div>
  <p class="abs center edit-link">&#9998; Edit profile image</p>

  <div class="abs field-label" style="top:256px"><svg width="8" height="9" viewBox="0 0 8 9"><circle cx="4" cy="2.3" r="2.2" fill="#0054AA"/><path d="M0 9a4 4 0 0 1 8 0z" fill="#0054AA"/></svg>Name:</div>
  <div class="abs field-value" style="top:258px"><span>Mara Quell</span><span>›</span></div>

  <div class="abs field-label" style="top:283px"><svg width="8" height="9" viewBox="0 0 8 9"><circle cx="4" cy="2.3" r="2.2" fill="#0054AA"/><path d="M0 9a4 4 0 0 1 8 0z" fill="#0054AA"/></svg>Username:</div>
  <div class="abs field-value" style="top:285px"><span>@username</span><span>›</span></div>

  <div class="abs field-label" style="top:312px"><svg width="10" height="8" viewBox="0 0 10 8"><rect width="10" height="8" rx="1" fill="#0054AA"/><path d="M0.5 1L5 4.5 9.5 1" stroke="#fff" fill="none"/></svg>Email:</div>
  <div class="abs field-value" style="top:314px"><span>name@mailbox.test</span><span>›</span></div>

  <div class="abs field-label" style="top:339px"><svg width="9" height="9" viewBox="0 0 9 9"><path d="M4 1H1v7h7V5M5 1h3v3M8 1L4 5" stroke="#0054AA" stroke-width="1.2" fill="none"/></svg>Links:</div>
  <div class="abs field-value" style="top:341px"><span>website.test</span></div>
  <div class="abs field-value" style="top:367px"><span>mylink.test</span></div>
  <div class="abs field-value" style="top:393px"><span>yourlink.test</span><span>&#8853;</span></div>

  <div class="abs field-label" style="top:420px"><svg width="9" height="9" viewBox="0 0 9 9"><rect width="9" height="9" rx="1.5" fill="#0054AA"/><path d="M2.5 6.5l1-2.5 2-2 1 1-2 2z" fill="#fff"/></svg>Bio:</div>
  <div class="abs field-value" style="top:422px"><span>A description of this user.</span><span>›</span></div>
</section>

</body>
</html>
```